Business card design for new eCommerce site focusing on integrity and strong businsess tactics

We need a business card that will stand out and be memorable. Something with color that matches our company logo colors. Think high end version of Pactivo. There are 2 logos provided. The parent company is called Amber Ledge Partners and we are presenting a new and very exciting eCommerce site called BrightHarborTrade.example.

Target Market(s)

Our target markets are in the Activities, Food and Beverage, Health and Beauty

Industry/Entity Type

Marketing

Contact Information for Business Card

We have 4 members that need cards...I will provide all info to the winner of the design contest
Business Address is
4870 West 63rd Avenue, Suite C207
Phoenix AZ 85731

Font styles to use
Serif
Sans Serif

Colors

Designer to choose colors to be used in the design.

Requirements
Must have
• The card must be memorable...should be unique in design but must exude integrity and be playful .
• I have provided several colors or our parent company...please feel free to use which ever
Nice to have
• I will leave this up to you. Feel free to use other images of your choosing that wraps around our client.....Activities, Dining, Health, Beauty
Should not have
• just dont be boring

```html
<!DOCTYPE html>
<html lang="en">
<head>
<meta charset="utf-8">
<title>Business Card – BrightHarborTrade.example</title>
<link rel="stylesheet" href="https://fonts.googleapis.com/css2?family=Montserrat:wght@400;500;700;800&display=swap">
<style>
  :root {
    --brand-blue: #2c7bb4;
    --brand-blue-deep: #1f6ea7;
    --brand-green: #7cc142;
    --ink-grey: #6b6b6b;
    --paper: #ffffff;
    --backdrop: #e9ebee;
  }
  * { box-sizing: border-box; margin: 0; padding: 0; }
  html, body {
    width: 1200px; height: 900px; overflow: hidden;
    background: var(--backdrop);
    font-family: "Montserrat", Arial, sans-serif;
  }
  .sheet {
    width: 1200px; height: 900px;
    display: flex; flex-direction: column;
    align-items: center; justify-content: center; gap: 40px;
  }
  .card {
    position: relative;
    width: 700px; height: 400px;
    border-radius: 22px;
    overflow: hidden;
    box-shadow: 0 6px 18px rgba(0,0,0,0.12);
  }

  /* Back side: parent company */
  .card--parent {
    background: var(--brand-blue);
    color: var(--paper);
    display: flex; flex-direction: column;
    align-items: center; justify-content: center;
  }
  .parent-mark {
    width: 62px; height: 62px;
    border: 4px solid var(--paper);
    border-radius: 50%;
    margin-bottom: 22px;
  }
  .parent-name {
    font-weight: 800; font-size: 44px; letter-spacing: 1px;
  }
  .parent-web {
    margin-top: 22px;
    font-weight: 500; font-size: 15px; letter-spacing: 2.5px;
  }

  /* Front side: eCommerce brand */
  .card--brand { background: var(--paper); }
  .brand-logo {
    position: absolute; left: 42px; top: 36px;
    display: flex; align-items: center; gap: 12px;
  }
  .brand-dot {
    width: 22px; height: 22px; border-radius: 50%;
    background: var(--brand-green);
  }
  .brand-name {
    font-weight: 700; font-size: 28px; color: var(--brand-blue);
  }
  .brand-tagline {
    position: absolute; left: 76px; top: 76px;
    font-size: 12px; letter-spacing: 1.2px; color: var(--ink-grey);
  }
  .divider {
    position: absolute; left: 70px; right: 60px; top: 160px;
    height: 1.5px; background: var(--brand-blue-deep);
  }
  .person {
    position: absolute; right: 60px; top: 100px; text-align: right;
  }
  .person-name {
    font-weight: 700; font-size: 22px; color: var(--brand-blue); letter-spacing: 0.5px;
  }
  .person-role {
    font-size: 17px; color: var(--ink-grey); letter-spacing: 0.8px;
  }
  .address {
    position: absolute; right: 60px; top: 176px; text-align: right;
    font-size: 16px; line-height: 1.5; color: var(--ink-grey); letter-spacing: 0.8px;
  }
  .contacts {
    position: absolute; left: 40px; top: 176px;
    list-style: none;
    font-size: 14px; line-height: 1.65; color: var(--ink-grey); letter-spacing: 0.6px;
  }
  .contacts li { display: flex; align-items: center; gap: 10px; }
  .contacts svg { width: 12px; height: 12px; flex: none; }
  .wave { position: absolute; left: 0; bottom: 0; width: 700px; height: 400px; }
</style>
</head>
<body>
<main class="sheet">

  <section class="card card--parent" aria-label="Card back">
    <div class="parent-mark"></div>
    <h1 class="parent-name">Amber Ledge Partners</h1>
    <p class="parent-web">www.amberledgepartners.example</p>
  </section>

  <section class="card card--brand" aria-label="Card front">
    <svg class="wave" viewBox="0 0 700 400" aria-hidden="true">
      <path d="M0,262 C170,330 330,352 470,330 C580,312 650,270 700,232 L700,400 L0,400 Z" fill="var(--brand-green)"/>
      <path d="M0,276 C170,344 330,364 470,342 C580,324 650,284 700,248 L700,400 L0,400 Z" fill="var(--paper)"/>
      <path d="M0,284 C160,360 300,400 460,360 C570,334 650,300 700,262 L700,400 L0,400 Z" fill="var(--brand-blue)"/>
      <path d="M0,300 C150,372 300,385 440,360 C360,372 200,355 0,318 Z" fill="var(--paper)"/>
    </svg>

    <div class="brand-logo">
      <span class="brand-dot"></span>
      <span class="brand-name">BrightHarborTrade.example</span>
    </div>
    <p class="brand-tagline">Activities-Dining-Health-Beauty</p>

    <div class="divider"></div>

    <div class="person">
      <p class="person-name">Daniel Reyes</p>
      <p class="person-role">Founder</p>
    </div>

    <address class="address" style="font-style:normal">
      4870 West 63rd Avenue,<br>
      Suite C207 Phoenix AZ 85731
    </address>

    <ul class="contacts">
      <li>
        <svg viewBox="0 0 12 12"><rect x="3" y="0.5" width="6" height="11" rx="1.2" fill="none" stroke="var(--brand-blue)" stroke-width="1.2"/></svg>
        0400 555 019
      </li>
      <li>
        <svg viewBox="0 0 12 12"><rect x="0.5" y="2" width="11" height="8" fill="var(--brand-blue)"/><path d="M0.5,2 L6,6.5 L11.5,2" fill="none" stroke="var(--paper)" stroke-width="1"/></svg>
        info@brightharbortrade.example
      </li>
      <li>
        <svg viewBox="0 0 12 12"><circle cx="5" cy="5" r="3.6" fill="none" stroke="var(--brand-blue)" stroke-width="1.6"/><path d="M7.6,7.6 L11,11" stroke="var(--brand-blue)" stroke-width="1.8"/></svg>
        www.brightharbortrade.example
      </li>
    </ul>
  </section>

</main>
</body>
</html>
```